Business Card - high end, modern health care

Hey designers!

We need a double sided business card for the boutique, cutting edge physical therapy rehabilitation centre in Sydney's Northern Beaches.

With the most qualified physios in the area The Harbourview Motion Clinic does what other physiotherapy practices do not, we take our time with our patients giving them longer appointments, better physios and therefor faster results!

We guarantee that the service people receive at THMC will be unparalleled.

Hence we need a business card to reflect our modern, boutique, high end service. The final design needs to reflect that we are in a class of our own yet with the feel of beachside retreat.

Below I have attached our logo in both blue on white and white on blue. The exact colour is;
and the font that we have used in our logo is Tex Gyre Aventador.

I like the idea of the blue as the main colour as it is more eye catching and our signage onto the main road will be in this blue and in the interest of consistency across marketing the blue needs to be a part of the design. However I would appreciate a few designs onto a wooden background as this is a visual theme within the fitout of the practice.

The design needs to be of standard size (91x55mm).

Target Market(s)

We target people who have an end outcome in mind and those who have had poor experiences with other providers and ensure that everyone gets the care that they deserve with a premium service that is tailored to the individuals circumstances. As a premium service, the target market is highly educated, business and tech savvy with the additional target market of elderly people who have self funded their retirement and see value in paying for the best ongoing rehabilitation to maintain independence.

Industry/Entity Type

Physical Therapy

Contact Information for Business Card

Name, designation( Titled Musculoskeletal Physiotherapist... there will also be those in the company that have multiple designations ie 5 or 6 words long), phone number, email, facebook, instagram, address

Font styles to use
Sans Serif

Colors

Designer to choose colors to be used in the design.

Requirements
Must have
• Front - The logo as large as possible, blue or wooden theme, and all of the important details.
• Back - A blank space/lines on which to write appointment times (no "Appointment, date, time" etc.)
Nice to have
• facebook url
• logos for facebook and instagram
• Mini logos for the phone and email?

```html
<!DOCTYPE html>
<html lang="en">
<head>
<meta charset="utf-8">
<title>The Harbourview Motion Clinic – Business Card</title>
<link href="https://fonts.googleapis.com/css2?family=Montserrat:wght@600&family=Questrial&display=swap" rel="stylesheet">
<style>
  :root {
    --brand-blue: #1155a5;
    --ink: #222428;
    --muted: #55585e;
    --rule: #6b6e73;
    --paper: #ffffff;
    --backdrop: #2f3a48;
    --pink: #e8518d;
    --sky: #2a9fe0;
  }
  * { box-sizing: border-box; margin: 0; padding: 0; }
  html, body { width: 1200px; height: 1200px; overflow: hidden; }
  body {
    background: var(--backdrop);
    display: flex; flex-direction: column; align-items: center; justify-content: center;
    gap: 56px;
    font-family: "Questrial", sans-serif;
  }
  .card {
    position: relative; width: 860px; height: 520px;
    background: var(--paper); border-radius: 44px; overflow: hidden;
    box-shadow: 0 10px 30px rgba(0,0,0,.35);
  }
  .card__art { position: absolute; inset: 0; }

  .wordmark { position: absolute; display: flex; align-items: center; gap: 14px; color: var(--brand-blue); }
  .wordmark__dot { width: 52px; height: 52px; border-radius: 50%; background: var(--brand-blue); flex: none; }
  .wordmark__text { font-family: "Montserrat", sans-serif; font-weight: 600; line-height: 1.05; }
  .wordmark__name { font-size: 30px; letter-spacing: .5px; display: block; }
  .wordmark__sub { font-size: 15px; letter-spacing: 6px; display: block; margin-top: 4px; }

  .front .wordmark { left: 470px; top: 200px; }

  .back__divider { position: absolute; left: 228px; top: 0; width: 2px; height: 100%; background: var(--rule); }
  .back .wordmark { left: 115px; top: 260px; transform: translate(-50%, -50%) rotate(-90deg); white-space: nowrap; }

  .rule { position: absolute; height: 2px; background: var(--rule); }
  .rule--top { left: 520px; right: 40px; top: 70px; }
  .rule--mid { left: 228px; right: 0; top: 240px; }
  .rule--low { left: 228px; right: 0; top: 410px; }
  .rule--write { left: 300px; right: 40px; top: 470px; height: 0; border-top: 2px dashed #9a9da2; background: none; }

  .person { position: absolute; left: 290px; top: 140px; }
  .person__name { font-size: 40px; color: var(--ink); }
  .person__name em { font-style: normal; color: var(--brand-blue); }
  .person__role { font-size: 20px; color: var(--muted); margin-top: 4px; }

  .contacts { position: absolute; left: 290px; top: 270px; list-style: none; display: grid; grid-template-columns: 330px 230px; row-gap: 18px; column-gap: 10px; }
  .contacts li { display: flex; align-items: center; gap: 14px; font-size: 22px; color: var(--ink); }
  .contacts .icon { width: 28px; height: 28px; flex: none; }
  .icon--social { border-radius: 50%; }
  .icon--fb { background: var(--sky); }
  .icon--ig { background: var(--pink); }
</style>
</head>
<body>

  <section class="card front" aria-label="Card front">
    <svg class="card__art" viewBox="0 0 860 520" aria-hidden="true">
      <path d="M0 0 H400 C330 170 360 420 600 520 H0 Z" fill="var(--brand-blue)"/>
      <circle cx="200" cy="300" r="132" fill="var(--paper)"/>
    </svg>
    <div class="wordmark">
      <span class="wordmark__dot"></span>
      <span class="wordmark__text">
        <span class="wordmark__name">THE HARBOURVIEW</span>
        <span class="wordmark__sub">MOTION CLINIC</span>
      </span>
    </div>
  </section>

  <section class="card back" aria-label="Card back">
    <div class="wordmark">
      <span class="wordmark__dot"></span>
      <span class="wordmark__text">
        <span class="wordmark__name">THE HARBOURVIEW</span>
        <span class="wordmark__sub">MOTION CLINIC</span>
      </span>
    </div>
    <div class="back__divider"></div>
    <div class="rule rule--top"></div>

    <div class="person">
      <p class="person__name">Name of <em>Person</em></p>
      <p class="person__role">Designation</p>
    </div>
    <div class="rule rule--mid"></div>

    <ul class="contacts">
      <li>
        <svg class="icon" viewBox="0 0 28 28" aria-hidden="true">
          <circle cx="14" cy="14" r="12" fill="none" stroke="var(--ink)" stroke-width="2.5"/>
          <path d="M10 8 l3 3 -2 2 c1 2 2 3 4 4 l2-2 3 3 -2 2 c-5 0-10-5-10-10z" fill="var(--ink)"/>
        </svg>
        555.013.2046
      </li>
      <li>
        <span class="icon icon--social icon--ig" aria-hidden="true"></span>
        instagram_name
      </li>
      <li>
        <svg class="icon" viewBox="0 0 28 28" aria-hidden="true">
          <rect x="2" y="6" width="24" height="16" fill="var(--ink)"/>
          <path d="M3 7 L14 16 L25 7" fill="none" stroke="var(--paper)" stroke-width="2"/>
        </svg>
        companyname@email.com
      </li>
      <li></li>
      <li>
        <span class="icon icon--social icon--fb" aria-hidden="true"></span>
        facebook/name
      </li>
    </ul>
    <div class="rule rule--low"></div>
    <div class="rule rule--write"></div>
  </section>

</body>
</html>
```